Dental specialist needs a sharp looking letterhead

I am looking for a letterhead to be used to send letters and communication between myself (a dental specialist) and other dentists.
My office is a state of the art dental specialty office.
I need to letterhead to also state:
Bertram L. Oswick DDS
2748 Tollard Avenue, Suite K
West Tollard, NY 14391
(716)392-5061
fax: (716)392-5087
oswickroot.com (**this email address may change)

i included my logo designs.
thank you

Target Market(s)

dentists

Industry/Entity Type

Communication

Requirements
Must have
• the included logo, whether the vertical or horizontal versions

```html
<!DOCTYPE html>
<html lang="en">
<head>
<meta charset="utf-8">
<title>Keystone Endodontics P.C. – Letterhead</title>
<link rel="stylesheet" href="https://fonts.googleapis.com/css2?family=Roboto+Slab:wght@300;400;700&display=swap">
<style>
  :root {
    --brand-blue: #45a3db;
    --brand-green: #8dc63f;
    --ink: #1d1d1b;
    --ink-soft: #3a3a3a;
    --paper: #ffffff;
    --rule: #555555;
    --mark-tint: #edf3fa;
  }
  * { margin: 0; padding: 0; box-sizing: border-box; }
  html, body { width: 931px; height: 1200px; overflow: hidden; background: var(--paper); }
  .letterhead {
    position: relative;
    width: 931px;
    height: 1200px;
    background: var(--paper);
    font-family: "Roboto Slab", serif;
    color: var(--ink-soft);
  }
  .brand {
    position: absolute;
    left: 35px;
    top: 34px;
    display: flex;
    align-items: center;
    height: 96px;
  }
  .brand-dot {
    width: 70px;
    height: 70px;
    border-radius: 50%;
    background: var(--brand-blue);
    margin-right: 14px;
  }
  .brand-rule {
    width: 1px;
    height: 96px;
    background: var(--rule);
    margin-right: 8px;
  }
  .brand-name {
    font-weight: 700;
    color: var(--ink);
    line-height: 1;
  }
  .brand-name .title { display: block; font-size: 31px; letter-spacing: -0.5px; }
  .brand-name .sub { display: block; font-size: 13px; letter-spacing: 2px; margin-top: 6px; padding-left: 26px; }

  .contact {
    position: absolute;
    left: 661px;
    top: 34px;
    height: 94px;
    padding-left: 12px;
    border-left: 1px solid var(--rule);
    font-weight: 300;
  }
  .contact .doctor {
    font-size: 20px;
    color: var(--brand-blue);
    line-height: 1;
    margin-top: 2px;
    margin-bottom: 10px;
    font-weight: 400;
  }
  .contact .doctor .degree { color: var(--brand-green); }
  .contact ul { list-style: none; }
  .contact li {
    font-size: 15.5px;
    line-height: 21px;
    display: flex;
    align-items: center;
    white-space: nowrap;
    color: var(--ink-soft);
  }
  .contact svg { width: 13px; height: 13px; margin-right: 5px; flex: none; }

  .watermark {
    position: absolute;
    left: 210px;
    top: 300px;
    width: 520px;
    height: 520px;
    border-radius: 50%;
    background: var(--mark-tint);
  }

  .footer {
    position: absolute;
    left: 0;
    bottom: 0;
    width: 931px;
    height: 120px;
  }
  .footer svg.band { position: absolute; left: 0; top: 0; width: 931px; height: 120px; }
  .address {
    position: absolute;
    left: 0;
    right: 0;
    top: 69px;
    text-align: center;
    color: #ffffff;
    font-size: 18.5px;
    font-weight: 400;
    display: flex;
    justify-content: center;
    align-items: center;
    gap: 10px;
  }
  .address svg { width: 13px; height: 18px; }
</style>
</head>
<body>
<main class="letterhead">
  <header>
    <div class="brand">
      <span class="brand-dot"></span>
      <span class="brand-rule"></span>
      <span class="brand-name">
        <span class="title">KEYSTONE</span>
        <span class="sub">Endodontics P.C.</span>
      </span>
    </div>

    <address class="contact">
      <p class="doctor">Bertram L. Oswick, <span class="degree">DDS</span></p>
      <ul>
        <li>
          <svg viewBox="0 0 14 14" aria-hidden="true"><circle cx="7" cy="7" r="6" fill="none" stroke="#45a3db" stroke-width="1.2"/><path d="M5 4.2c-.8.6-.6 2.4.7 3.9s3 2.1 3.6 1.3l-.9-1-1 .4c-.6-.3-1.2-1-1.4-1.6l.5-.9z" fill="#45a3db"/></svg>
          (716)392-5061
        </li>
        <li>
          <svg viewBox="0 0 14 14" aria-hidden="true"><rect x="4" y="2" width="6" height="4" fill="#8dc63f"/><rect x="1" y="6" width="12" height="5" rx="1" fill="#8dc63f"/><rect x="3" y="11" width="2" height="2" fill="#8dc63f"/><rect x="9" y="11" width="2" height="2" fill="#8dc63f"/></svg>
          (716)392-5087
        </li>
        <li>
          <svg viewBox="0 0 14 14" aria-hidden="true"><rect x="1" y="3" width="12" height="8.5" fill="#45a3db"/><path d="M1 3l6 4.5L13 3" fill="none" stroke="#ffffff" stroke-width="1"/></svg>
          oswickroot@tollardmail.com
        </li>
      </ul>
    </address>
  </header>

  <div class="watermark" aria-hidden="true"></div>

  <footer class="footer">
    <svg class="band" viewBox="0 0 931 120" preserveAspectRatio="none" aria-hidden="true">
      <path d="M0 60 Q465 -30 931 60" fill="none" stroke="#45a3db" stroke-width="5"/>
      <path d="M0 80 Q465 -5 931 80" fill="none" stroke="#8dc63f" stroke-width="4"/>
      <path d="M0 94 Q465 10 931 94 L931 120 L0 120 Z" fill="#45a3db"/>
    </svg>
    <p class="address">
      <svg viewBox="0 0 13 18" aria-hidden="true"><path d="M6.5 0C2.9 0 0 2.8 0 6.3 0 11 6.5 18 6.5 18S13 11 13 6.3C13 2.8 10.1 0 6.5 0z" fill="#ffffff"/><circle cx="6.5" cy="6.3" r="2.4" fill="#45a3db"/></svg>
      2748 Tollard Avenue, Suite K, West Tollard, NY 14391
    </p>
  </footer>
</main>
</body>
</html>
```